Stationary For Commercial Real Estate Company

We need a consistently branded image for our business cards, letterhead, property marketing flyers, powerpoint presentations, etc.

We are a COMMERCIAL real estate company. We do NOT do residential real estate, so please do not submit any designs with references to houses as they will be rejected.

We just completed a design contest for our logo, so we want to encorporate that logo in our stationary design, and we have attached it for your use. Please let us know if you need the logo in another format.

We can accept the business cards in adobe illustrator, the letterhead needs to be a template in Microsoft Word, the Property Flyer can be either in PowerPoint or Adobe Illustrator, and the PowerPoint presentation needs to have a Cover Page, Table of Contents, a few sample pages, and a Closing/Summary slide at the end.

We have attached a sample Property Flyer to show what we are basically looking for; but this is only provided as a sample, so you can see the kind of information we generally need to include on our Flyers. They can be in either landscape or portrait layout.

Target Market(s)

CEO and Upper Level managers who are decision makers regarding commercial real estate projects. Local, regional and fortune 500 clients.

Industry/Entity Type

Real Estate

Requirements
Must have
• There must be a space on the Flyer that includes the disclaimer shown on the bottom of the attached sample.
Nice to have
• I appreciate the designs submitted so far, but I'd prefer not to have watermarks on the letterhead or business cards. I'm not sure I'm a big fan of the watermarks.

Also, I'd like to see some color combinations that use something other than just red. I'd like to see something where we have just the logo in red and use other contrasting colors on the letterhead or business cards.
Should not have
• Please, no references to houses or anything else that suggests residential real estate. We only do commercial real estate.

```html
<!DOCTYPE html>
<html lang="en">
<head>
<meta charset="utf-8">
<title>Harlan Reeve – Presentation Template</title>
<link href="https://fonts.googleapis.com/css2?family=Jost:wght@400;500;600&display=swap" rel="stylesheet">
<style>
  :root {
    --sheet: #000000;
    --slide: #ffffff;
    --brand-red: #be1e2d;
    --title-red: #a01d26;
    --brand-orange: #f7941d;
    --muted: #8a3a3a;
    --white: #ffffff;
  }
  * { margin: 0; padding: 0; box-sizing: border-box; }
  html, body {
    width: 848px; height: 1200px; overflow: hidden;
    background: var(--sheet);
    font-family: "Jost", "Futura", sans-serif;
  }
  .canvas { position: relative; width: 848px; height: 1200px; }
  .slide { position: absolute; left: 36px; width: 776px; background: var(--slide); }
  .slide--cover { top: 53px; height: 533px; }
  .slide--content { top: 617px; height: 534px; }

  /* Cover */
  .cover-panel {
    position: absolute; left: 31px; top: 0; width: 214px; height: 416px;
    background: var(--brand-red); color: var(--white);
  }
  .brand-name {
    position: absolute; left: 20px; top: 108px;
    display: flex; align-items: center; gap: 8px;
    font-weight: 600; font-size: 21px; letter-spacing: 0.5px; line-height: 1;
  }
  .brand-name .mark { width: 12px; height: 12px; background: var(--white); }
  .brand-tagline {
    position: absolute; left: 20px; top: 138px;
    font-weight: 500; font-size: 12.5px; letter-spacing: 0.2px;
  }
  .cover-accent {
    position: absolute; left: 31px; top: 429px; width: 214px; height: 87px;
    background: var(--brand-orange);
  }
  .program-title {
    position: absolute; left: 285px; top: 247px;
    color: var(--title-red); font-weight: 600; font-size: 45px; line-height: 1;
  }
  .program-subtitle {
    position: absolute; left: 286px; top: 300px;
    color: var(--title-red); font-weight: 600; font-size: 21px; line-height: 1;
  }
  .cover-url {
    position: absolute; right: 24px; top: 502px;
    color: var(--muted); font-size: 13px;
  }

  /* Content slide */
  .header-bar {
    position: absolute; left: 22px; top: 16px; width: 635px; height: 60px;
    background: var(--brand-red);
  }
  .slide-title {
    position: absolute; left: 26px; top: 13px;
    color: var(--white); font-weight: 600; font-size: 30px; line-height: 1.1;
  }
  .header-brand {
    position: absolute; left: 663px; top: 16px; width: 97px; height: 60px;
    display: flex; align-items: center; justify-content: center;
    color: var(--brand-orange); font-weight: 600; font-size: 26px; letter-spacing: 1px;
  }
  .footer-bar {
    position: absolute; left: 22px; top: 490px; width: 635px; height: 27px;
    background: var(--brand-red);
  }
  .footer-url {
    position: absolute; right: 14px; top: 5px;
    color: var(--white); font-size: 13px;
  }
  .footer-accent {
    position: absolute; left: 664px; top: 490px; width: 87px; height: 27px;
    background: var(--brand-orange);
  }
</style>
</head>
<body>
<div class="canvas">
  <section class="slide slide--cover">
    <div class="cover-panel">
      <div class="brand-name"><span class="mark"></span>HARLAN REEVE</div>
      <div class="brand-tagline">COMMERCIAL REAL ESTATE</div>
    </div>
    <div class="cover-accent"></div>
    <h1 class="program-title">Program Title</h1>
    <h2 class="program-subtitle">Program Sub Title</h2>
    <div class="cover-url">www.HRCRE.com</div>
  </section>

  <section class="slide slide--content">
    <div class="header-bar">
      <h1 class="slide-title">Title Contents</h1>
    </div>
    <div class="header-brand">HR</div>
    <div class="footer-bar">
      <div class="footer-url">www.HRCRE.com</div>
    </div>
    <div class="footer-accent"></div>
  </section>
</div>
</body>
</html>
```